Marlowe Group needs a business card

I would like the card to be simple but modern and elegant.
I like black and white.
or black and gold.
we are a private finance lender and also are involved in property and property developments.

please look at the business card photos i provided i would like M.G only one one side and all the other details on the other side use fonts that tie in with my theme.

Industry/Entity Type

Finance

Contact Information for Business Card

Marlowe Group (M.G) Daniel Marlowe M: 0413586207 E: danmarl@inboxmail.test

Font styles to use
Other font styles liked:
• Use fonts that would reflect our business

Colors
000000
ffffff

Requirements
Must have
• one side of details
• other side has either M.G or Marlowe Group like in the photos provided

```html
<!DOCTYPE html>
<html lang="en">
<head>
<meta charset="UTF-8">
<title>Marlowe Group — Business Card</title>
<link rel="stylesheet" href="https://fonts.googleapis.com/css2?family=Montserrat:wght@400;500;700&display=swap">
<style>
  :root {
    --stage: #1c1c1c;
    --card-light: #ffffff;
    --card-dark: #232323;
    --ink: #1a1a1a;
    --ink-soft: #4a4a4a;
    --rule: #9a9a9a;
    --paper-text: #f2f2f2;
  }
  * { margin: 0; padding: 0; box-sizing: border-box; }
  html, body {
    width: 1200px;
    height: 786px;
    overflow: hidden;
    background: var(--stage);
    font-family: "Montserrat", Arial, sans-serif;
  }
  .stage {
    position: relative;
    width: 1200px;
    height: 786px;
    display: flex;
    align-items: center;
    justify-content: center;
    gap: 60px;
  }
  .card {
    position: relative;
    width: 510px;
    height: 312px;
    border-radius: 3px;
    box-shadow: 0 14px 34px rgba(0, 0, 0, 0.45);
  }
  .card--details {
    background: var(--card-light);
    color: var(--ink);
  }
  .details__name-block {
    position: absolute;
    top: 34px;
    right: 36px;
    text-align: right;
  }
  .details__name {
    font-weight: 700;
    font-size: 15px;
    letter-spacing: 0.6px;
    text-transform: uppercase;
  }
  .details__rule {
    display: block;
    margin-top: 10px;
    margin-left: auto;
    width: 150px;
    height: 1px;
    background: var(--rule);
  }
  .details__contact {
    position: absolute;
    left: 36px;
    bottom: 30px;
    list-style: none;
    font-weight: 400;
    font-size: 13px;
    line-height: 1.6;
    color: var(--ink-soft);
    letter-spacing: 0.3px;
  }
  .card--brand {
    background: var(--card-dark);
    display: flex;
    align-items: center;
    justify-content: center;
  }
  .brand__name {
    font-weight: 500;
    font-size: 30px;
    letter-spacing: 3px;
    color: var(--paper-text);
  }
</style>
</head>
<body>
  <main class="stage">
    <section class="card card--details" aria-label="Card front with contact details">
      <div class="details__name-block">
        <h1 class="details__name">Daniel Marlowe</h1>
        <span class="details__rule"></span>
      </div>
      <ul class="details__contact">
        <li>M: 0413586207</li>
        <li>E: danmarl@inboxmail.test</li>
      </ul>
    </section>

    <section class="card card--brand" aria-label="Card back with company name">
      <p class="brand__name">Marlowe Group</p>
    </section>
  </main>
</body>
</html>
```